New travel store signage for Marlow Journeys to attract luxury travellers.

Hello,
We are looking to change the signage of our stores. The signage must include the following:
1. Marlow Journeys Logo (attached)
2. The text...The Travel & Cruise Experts
3. Brand Colours ( Fb0196, 412266, d41d84 and ffffff)
Please note the signage design must be central and only cover two thirds of the store front. We have also attached an image of one of our new stores which might be helpful when preparing a mock up.

We are looking for a quick turnaround on this, making a decision within 48 hours.

Target Market(s)

Retail

Industry/Entity Type

Travel Agency

Font styles to use
Other font styles liked:
• Radley

Colors
E54698
E96AAD
F1A4CE
F9D9EA
FCEFF6
6B429C
8869AF
B7A5CE
E3DAEB
F3F0F8

Requirements
Must have
• Hello, We are looking to change the signage of our stores. The signage must include the following: 1. Marlow Journeys Logo (attached) 2. The text...The Travel & Cruise Experts 3. Brand Colours ( Fb0196, 412266, d41d84 and ffffff) Please note the signage design must be central and only cover two thirds of the store front.
Should not have
• different colour or fonts. Gradient design.

```html
<!DOCTYPE html>
<html lang="en">
<head>
<meta charset="utf-8">
<title>Marlow Journeys – Store Signage &amp; Card</title>
<link rel="stylesheet" href="https://fonts.googleapis.com/css2?family=Radley&family=Montserrat:ital,wght@0,500;1,600&display=swap">
<style>
  :root {
    --navy: #272262;
    --pink: #e91e8c;
    --plum: #6b2170;
    --white: #ffffff;
    --backdrop: #b3b3b3;
  }
  * { margin: 0; padding: 0; box-sizing: border-box; }
  html, body {
    width: 1200px;
    height: 1020px;
    overflow: hidden;
    background: var(--backdrop);
  }
  .canvas { position: relative; width: 1200px; height: 1020px; }

  .sign, .card {
    position: absolute;
    background: var(--white);
    overflow: hidden;
  }
  .sign { left: 20px; top: 203px; width: 1161px; height: 275px; }
  .card { left: 306px; top: 674px; width: 540px; height: 300px; }

  .swoosh { position: absolute; inset: 0; width: 100%; height: 100%; }

  .brand-lockup {
    position: absolute;
    left: 0; right: 0;
    display: flex;
    align-items: center;
    justify-content: center;
    gap: 14px;
  }
  .brand-dot {
    border-radius: 50%;
    background: var(--pink);
    flex: none;
  }
  .brand-name {
    font-family: "Radley", serif;
    color: var(--navy);
    white-space: nowrap;
    line-height: 1;
  }

  .sign .brand-lockup { top: 118px; }
  .sign .brand-dot { width: 30px; height: 30px; }
  .sign .brand-name { font-size: 54px; }

  .tagline {
    position: absolute;
    left: 0; right: 0;
    top: 233px;
    text-align: center;
    font-family: "Montserrat", sans-serif;
    font-style: italic;
    font-weight: 600;
    font-size: 25px;
    color: var(--navy);
  }

  .card .brand-lockup { top: 104px; gap: 10px; }
  .card .brand-dot { width: 20px; height: 20px; }
  .card .brand-name { font-size: 32px; }

  .contact {
    position: absolute;
    left: 0; right: 0;
    top: 196px;
    text-align: center;
    font-family: "Montserrat", sans-serif;
    font-weight: 500;
    color: var(--navy);
  }
  .contact-phone {
    display: flex;
    align-items: center;
    justify-content: center;
    gap: 5px;
    font-size: 22px;
    line-height: 28px;
  }
  .phone-icon { width: 23px; height: 23px; }
  .contact-web { font-size: 18px; line-height: 26px; }
</style>
</head>
<body>
<main class="canvas">

  <section class="sign">
    <svg class="swoosh" viewBox="0 0 1935 459" preserveAspectRatio="none" aria-hidden="true">
      <defs>
        <linearGradient id="band-left" x1="0" y1="1" x2="1" y2="0">
          <stop offset="0" stop-color="var(--plum)"/>
          <stop offset="0.6" stop-color="var(--pink)"/>
        </linearGradient>
        <linearGradient id="band-right" x1="1" y1="0" x2="0" y2="1">
          <stop offset="0" stop-color="var(--plum)"/>
          <stop offset="0.5" stop-color="var(--pink)"/>
        </linearGradient>
      </defs>
      <path d="M0 0 H557 Q200 110 0 437 Z" fill="url(#band-left)"/>
      <path d="M0 0 H520 Q180 80 0 312 Z" fill="var(--white)"/>
      <path d="M0 0 H500 Q170 70 0 275 Z" fill="var(--navy)"/>

      <path d="M1935 32 Q1700 390 1370 459 H1935 Z" fill="url(#band-right)"/>
      <path d="M1935 120 Q1720 410 1415 459 H1935 Z" fill="var(--white)"/>
      <path d="M1935 163 Q1730 425 1440 459 H1935 Z" fill="var(--navy)"/>
    </svg>

    <div class="brand-lockup">
      <span class="brand-dot"></span>
      <span class="brand-name">Marlow Journeys</span>
    </div>
    <p class="tagline">The Travel &amp; Cruise Experts</p>
  </section>

  <section class="card">
    <svg class="swoosh" viewBox="0 0 900 499" preserveAspectRatio="none" aria-hidden="true">
      <defs>
        <linearGradient id="card-band-top" x1="0" y1="0" x2="1" y2="1">
          <stop offset="0.3" stop-color="var(--pink)"/>
          <stop offset="1" stop-color="var(--plum)"/>
        </linearGradient>
        <linearGradient id="card-band-bottom" x1="0" y1="0" x2="1" y2="1">
          <stop offset="0" stop-color="var(--pink)"/>
          <stop offset="1" stop-color="var(--plum)"/>
        </linearGradient>
      </defs>
      <path d="M570 0 Q820 90 900 302 V0 Z" fill="url(#card-band-top)"/>
      <path d="M620 0 Q835 70 900 195 V0 Z" fill="var(--white)"/>
      <path d="M640 0 Q845 65 900 177 V0 Z" fill="var(--navy)"/>

      <path d="M0 132 Q150 400 415 499 H0 Z" fill="url(#card-band-bottom)"/>
      <path d="M0 262 Q150 435 395 499 H0 Z" fill="var(--white)"/>
      <path d="M0 272 Q150 445 378 499 H0 Z" fill="var(--navy)"/>
    </svg>

    <div class="brand-lockup">
      <span class="brand-dot"></span>
      <span class="brand-name">Marlow Journeys</span>
    </div>

    <div class="contact">
      <p class="contact-phone">
        <svg class="phone-icon" viewBox="0 0 24 24" aria-hidden="true">
          <circle cx="12" cy="12" r="12" fill="var(--pink)"/>
          <path d="M8.2 5.8 l2 2.4 q0.4 0.6 -0.1 1.1 l-0.9 0.9 q1.2 2.5 3.9 3.9 l0.9 -0.9 q0.5 -0.5 1.1 -0.1 l2.4 2 q0.5 0.5 0 1.1 l-1.2 1.2 q-1 1 -3 0.2 q-5 -2.4 -7.2 -7.2 q-0.8 -2 0.2 -3 l1.2 -1.2 q0.6 -0.5 1.1 0 Z" fill="var(--white)"/>
        </svg>
        0300 555 0142
      </p>
      <p class="contact-web">www.marlowjourneys.com</p>
    </div>
  </section>

</main>
</body>
</html>
```